QuillVane needs a dashboard page designed

Redesign the dashboard shown in the provided images.

There are two images:
- dashboard.png
- dashboard-expanded.png

NOTE: The vocabulary navigation on the left will be a very long list of words 100s, so keep that in mind when you're designing both the vocab navigation and the expanded vocab popup.

In the dashboard.png picture, there needs to be a progress chart showing the word progress like the following: review 1(show it as completed) -> review 2(show the user they are here) -> review 3(unvisited) -> review 4(unvisited)

The do-not-design-this-page.png image is for your reference only. It is not to be designed. Use it to understand the overall look and feel of the website to help you create the best dashboard page possible.
Updates

Need extra days to review

Industry/Entity Type

Education English learning

Number of Pages Required

1 page

Requirements
Must have
• The main navigation and main header cannot change between pages. See the do-not-design page for the main navigateion and header.
Should not have
• Do not add a person profile. We will not have images of our users. Keep the icons in the main navigation as they are.

```html
<!DOCTYPE html>
<html lang="en">
<head>
<meta charset="utf-8">
<title>QuillVane – Vocabulary Dashboard</title>
<link rel="stylesheet" href="https://fonts.googleapis.com/css2?family=Figtree:wght@400;500;600;700&display=swap">
<style>
  :root{
    --ink:#1c1a1b;
    --text:#222;
    --muted:#8a8a8a;
    --panel:#e1f3fc;
    --white:#fff;
    --blue:#0a7cc6;
    --orange:#f9a21a;
    --grey:#d8d8d8;
    --band-long:#e6ebfc;
    --band-work:#d4fffa;
    --band-short:#fffde6;
    --band-forgot:#e4fbfb;
    --modal:#262626;
    --chip:#a9dcf5;
    --chip-active:#3d8bfd;
    --line:#d0e3ec;
  }
  html,body{margin:0;padding:0;background:var(--white);}
  body{width:885px;height:1200px;overflow:hidden;font-family:"Figtree",sans-serif;}
  svg{display:block;font-family:"Figtree",sans-serif;}
  .frame-dark{fill:var(--ink);}
  .logo{fill:var(--white);font-weight:700;font-size:12.5px;}
  .nav-label{fill:var(--white);font-size:5.6px;font-weight:500;}
  .icon-w{fill:var(--white);}
  .side-panel{fill:var(--panel);}
  .sec-head{fill:var(--text);font-size:7px;font-weight:500;}
  .sec-item{fill:var(--muted);font-size:6.8px;}
  .rule{stroke:var(--line);stroke-width:.6;}
  .pill-out{fill:none;stroke:var(--blue);stroke-width:.8;}
  .small{fill:var(--text);font-size:7px;}
  .step-label{fill:var(--text);font-size:7.6px;text-anchor:middle;}
  .step-num{fill:var(--white);font-size:9.5px;font-weight:700;text-anchor:middle;}
  .card{fill:var(--panel);}
  .word-title{fill:var(--text);font-size:12.5px;font-weight:600;}
  .btn{fill:var(--orange);}
  .btn-text{fill:var(--ink);font-size:8.4px;font-weight:500;text-anchor:middle;}
  .body-text{fill:var(--text);font-size:7.6px;}
  .graph-title{fill:var(--text);font-size:10.5px;font-weight:600;text-anchor:middle;}
  .band-label{fill:var(--text);font-size:6px;}
  .tick{fill:var(--text);font-size:6.8px;text-anchor:middle;}
  .axis{stroke:var(--ink);stroke-width:.6;}
  .bar{fill:var(--blue);}
  .curve{fill:none;stroke:var(--blue);stroke-width:.7;stroke-dasharray:1 1.2;}
  .h2{fill:var(--text);font-size:13px;font-weight:600;}
  .foot{fill:var(--text);font-size:8px;text-anchor:middle;}
  .tag{fill:var(--text);font-size:7.5px;}
  .dim{fill:rgba(0,0,0,.58);}
  .modal{fill:var(--modal);}
  .m-head{fill:var(--white);font-size:10.5px;font-weight:500;}
  .m-small{fill:var(--white);font-size:6.5px;}
  .chip{fill:var(--chip);}
  .chip-text{fill:#1d3b4a;font-size:6.6px;text-anchor:middle;}
  .chip-active{fill:var(--chip-active);}
  .chip-active-text{fill:var(--white);font-size:7.8px;text-anchor:middle;}
</style>
</head>
<body>
<svg width="885" height="1200" viewBox="0 0 885 1200" role="group" aria-label="QuillVane vocabulary dashboard and expanded vocabulary list">
  <defs>
    <g id="dashboard">
      <!-- app shell -->
      <rect class="frame-dark" x="55" y="35" width="774" height="31"/>
      <rect class="frame-dark" x="55" y="35" width="52" height="540"/>
      <text class="logo" x="107" y="54">QuillVane</text>
      <g class="icon-w">
        <circle cx="755" cy="50" r="3.4"/><circle cx="755" cy="50" r="1.4" fill="var(--ink)"/>
        <ellipse cx="778" cy="50" rx="4" ry="3.3"/><path d="M775 52 l-1 3 3-1.5z"/>
        <circle cx="800" cy="48" r="2.2"/><path d="M795.6 54.5 a4.4 3.2 0 0 1 8.8 0z"/>
      </g>
      <!-- main nav -->
      <g class="icon-w">
        <path d="M81 83 l5-4.5 5 4.5 v5 h-3.5 v-3 h-3 v3 H81z"/>
        <path d="M82 114 l2.5-1.5 3 1.5 3-1.5 v6 l-3 1.5-3-1.5-2.5 1.5z"/>
        <rect x="78.5" y="148" width="5" height="8"/>
      </g>
      <text class="nav-label" x="81" y="96" text-anchor="middle">Best Tutor</text>
      <text class="nav-label" x="81" y="130" text-anchor="middle">Daily English</text>
      <text class="nav-label" x="81" y="166" text-anchor="middle">Business</text>

      <!-- vocabulary navigation -->
      <rect class="side-panel" x="126" y="76" width="132" height="445" rx="4"/>
      <rect class="pill-out" x="134" y="84" width="41" height="17" rx="8.5" fill="var(--white)"/>
      <text class="small" x="140" y="95.5" font-size="8">ALL</text>
      <path d="M164 91 l2 2 2-2" fill="none" stroke="var(--text)" stroke-width=".8"/>
      <text class="small" x="207" y="94.5" font-size="6.6">EXPAND</text>
      <path d="M238 90.5 v-1.5 h1.5 M244 90.5 v-1.5 h-1.5 M238 94 v1.5 h1.5 M244 94 v1.5 h-1.5" fill="none" stroke="var(--text)" stroke-width=".7"/>

      <circle cx="133.5" cy="126" r="3" fill="var(--ink)"/>
      <text class="sec-head" x="142" y="128.5">SHORT - TERM MEMORY</text>
      <circle cx="234" cy="126" r="3" fill="var(--ink)"/>
      <line class="rule" x1="128" y1="135" x2="258" y2="135"/>
      <text class="sec-item" x="143" y="145.5">Grab</text>
      <line class="rule" x1="128" y1="149.5" x2="258" y2="149.5"/>

      <rect x="131" y="167.5" width="5" height="5" fill="var(--ink)"/>
      <text class="sec-head" x="142" y="173">WORKING MEMORY</text>
      <circle cx="234" cy="170.5" r="3" fill="var(--ink)"/>
      <line class="rule" x1="128" y1="180" x2="258" y2="180"/>
      <g>
        <text class="sec-item" x="142" y="191.5">Cool Down</text>
        <line class="rule" x1="128" y1="195.5" x2="258" y2="195.5"/>
        <text class="sec-item" x="142" y="204.8">Crave</text>
        <line class="rule" x1="128" y1="208.8" x2="258" y2="208.8"/>
        <text class="sec-item" x="142" y="218.1">Go For</text>
        <line class="rule" x1="128" y1="222.1" x2="258" y2="222.1"/>
        <text class="sec-item" x="142" y="231.4">Go-To</text>
        <line class="rule" x1="128" y1="235.4" x2="258" y2="235.4"/>
        <text class="sec-item" x="142" y="244.7">In The Mood For</text>
        <line class="rule" x1="128" y1="248.7" x2="258" y2="248.7"/>
        <text class="sec-item" x="142" y="258">Sip</text>
        <line class="rule" x1="128" y1="262" x2="258" y2="262"/>
        <text class="sec-item" x="142" y="271.3">Soothing</text>
        <line class="rule" x1="128" y1="275.3" x2="258" y2="275.3"/>
        <text class="sec-item" x="142" y="284.6">Stick With</text>
        <line class="rule" x1="128" y1="288.6" x2="258" y2="288.6"/>
        <text class="sec-item" x="142" y="297.9">Throw in / Throw On</text>
        <line class="rule" x1="128" y1="301.9" x2="258" y2="301.9"/>
      </g>

      <rect x="131" y="317" width="5" height="4" rx=".6" fill="var(--ink)"/>
      <path d="M132 317 v-1.5 a1.5 1.5 0 0 1 3 0 v1.5" fill="none" stroke="var(--ink)" stroke-width=".8"/>
      <text class="sec-head" x="142" y="321.5">LONG - TERM MEMORY</text>
      <circle cx="234" cy="319" r="3" fill="var(--ink)"/>
      <line class="rule" x1="128" y1="329" x2="258" y2="329"/>
      <text class="sec-item" x="143" y="339.5">Give It A Try</text>
      <line class="rule" x1="128" y1="343.5" x2="258" y2="343.5"/>

      <!-- review progress -->
      <line x1="349" y1="98" x2="473" y2="98" stroke="var(--blue)" stroke-width="2.6"/>
      <line x1="473" y1="98" x2="721" y2="98" stroke="var(--grey)" stroke-width="2.6"/>
      <circle cx="349" cy="98" r="13" fill="var(--blue)"/>
      <circle cx="473" cy="98" r="13" fill="var(--orange)"/>
      <circle cx="597" cy="98" r="13" fill="var(--grey)"/>
      <circle cx="721" cy="98" r="13" fill="var(--grey)"/>
      <text class="step-num" x="349" y="101.5">01</text>
      <text class="step-num" x="473" y="101.5">02</text>
      <text class="step-num" x="597" y="101.5">03</text>
      <text class="step-num" x="721" y="101.5">04</text>
      <text class="step-label" x="349" y="122">Review 1</text>
      <text class="step-label" x="473" y="122">Review 2</text>
      <text class="step-label" x="597" y="122">Review 3</text>
      <text class="step-label" x="721" y="122">Review 4</text>

      <!-- word card -->
      <rect class="card" x="262" y="137" width="545" height="90" rx="5"/>
      <path d="M281.5 149.5 l1.9 4 4.3.5-3.2 3 .9 4.3-3.9-2.2-3.9 2.2.9-4.3-3.2-3 4.3-.5z" fill="var(--orange)"/>
      <text class="word-title" x="294" y="161">Grab</text>
      <rect class="btn" x="616" y="149" width="175" height="21" rx="10.5"/>
      <text class="btn-text" x="703.5" y="162.5">Start Vocabulary Review Exercise 3</text>
      <text class="body-text">
        <tspan x="278" y="186.5">The word "grab" is most commonly used as averb, meaning to take something quickly or suddenly. Imagine you're running late for</tspan>
        <tspan x="278" y="196">school. You don't have time for breakfast, so you quickly grab an apple from the kitchen and rush out the door. As you reach the bus</tspan>
        <tspan x="278" y="205.5">stop, your friend waves and says, "Hey! Let's grab a coffee after class." Later, when you sit down, your phone starts ringing. You grab it</tspan>
        <tspan x="278" y="215">from your bag and answer.</tspan>
      </text>

      <!-- learning curve -->
      <rect class="card" x="262" y="232" width="545" height="223" rx="5"/>
      <text class="graph-title" x="554" y="247">Learning Curve Graph</text>
      <rect x="278" y="254" width="518" height="37" fill="var(--band-long)"/>
      <rect x="278" y="291" width="518" height="86" fill="var(--band-work)"/>
      <rect x="278" y="377" width="518" height="17" fill="var(--band-short)"/>
      <rect x="278" y="394" width="518" height="17" fill="var(--band-forgot)"/>
      <text class="band-label" x="282" y="270">Long-Term Memory</text>
      <text class="band-label" x="281.5" y="310">Working Memory</text>
      <text class="band-label" x="282.5" y="387.5">Short- Term Memory</text>
      <text class="band-label" x="281.5" y="404">Forgotten Memory</text>
      <rect class="bar" x="348" y="377" width="10.5" height="34"/>
      <rect class="bar" x="399.5" y="291" width="10.5" height="120"/>
      <path class="curve" d="M358.5 377.5 Q389 380 398 410"/>
      <path class="curve" d="M410 291.5 Q478 290 518 411"/>
      <line class="axis" x1="278" y1="253" x2="278" y2="427"/>
      <line class="axis" x1="272" y1="411" x2="796" y2="411"/>
      <g class="axis">
        <line x1="304" y1="411" x2="304" y2="417"/><line x1="332" y1="411" x2="332" y2="417"/>
        <line x1="360" y1="411" x2="360" y2="417"/><line x1="387" y1="411" x2="387" y2="417"/>
        <line x1="411" y1="411" x2="411" y2="417"/><line x1="438" y1="411" x2="438" y2="417"/>
        <line x1="467" y1="411" x2="467" y2="417"/><line x1="496" y1="411" x2="496" y2="417"/>
        <line x1="522" y1="411" x2="522" y2="417"/><line x1="550" y1="411" x2="550" y2="417"/>
        <line x1="576" y1="411" x2="576" y2="417"/><line x1="604" y1="411" x2="604" y2="417"/>
        <line x1="634" y1="411" x2="634" y2="417"/><line x1="661" y1="411" x2="661" y2="417"/>
        <line x1="686" y1="411" x2="686" y2="417"/><line x1="710" y1="411" x2="710" y2="417"/>
        <line x1="734" y1="411" x2="734" y2="417"/><line x1="761" y1="411" x2="761" y2="417"/>
        <line x1="785" y1="411" x2="785" y2="417"/>
      </g>
      <g class="tick">
        <text x="304" y="425">18 May</text><text x="332" y="425">12:00</text>
        <text x="361" y="425">19 May</text><text x="387" y="425">12:00</text>
        <text x="412" y="425">20 May</text><text x="441" y="426">12:00</text>
        <text x="470" y="426">21 May</text><text x="496" y="425">12:00</text>
        <text x="523" y="425">22 May</text><text x="550" y="425">12:00</text>
        <text x="580" y="426">23 May</text><text x="607" y="425">12:00</text>
        <text x="636" y="426">24 May</text><text x="661" y="426">12:00</text>
        <text x="687" y="426">25 May</text><text x="710" y="426">12:00</text>
        <text x="736" y="426">26 May</text><text x="760" y="426">12:00</text>
        <text x="785" y="426">27 May</text>
      </g>
      <text class="graph-title" x="560" y="444" font-size="8.4">Date Range</text>

      <!-- analysis -->
      <text class="h2" x="272.5" y="473">QuillVane Tutor Learning Analysis</text>
      <text class="body-text">
        <tspan x="272.5" y="488">Lorem ipsum dolor sit amet, consectetur adipiscing elit. Nam rutrum commodo enim id bibendum. Nunc dignissim risus erat, nec</tspan>
        <tspan x="272.5" y="497.5">finibus nunc dictum eu. Aliquam sit amet euismod metus, quis malesuada erat. Sed at felis quis nulla feugiat cursus at at dolor.</tspan>
        <tspan x="272.5" y="507">Maecenas pretium aliquet dapibus. Fusce et eleifend massa. Sed convallis ex mi, at lobortis ligula congue vel. Pellentesque pharetra</tspan>
        <tspan x="272.5" y="516.5">molestie leo, sed vehicula felis commodo molestie.</tspan>
      </text>
      <text class="foot" x="442" y="557">© 2025 | www.quillvane.com</text>
      <text class="tag" x="808" y="565">M1</text>
    </g>
  </defs>

  <use href="#dashboard"/>
  <use href="#dashboard" transform="translate(-1 580)"/>

  <!-- expanded vocabulary view -->
  <rect class="dim" x="54" y="615" width="775" height="540"/>
  <rect class="modal" x="176" y="787" width="531" height="211" rx="11"/>
  <rect x="215.5" y="808.5" width="54.5" height="19" rx="3.5" fill="none" stroke="var(--white)" stroke-width=".8"/>
  <text class="m-small" x="224" y="820.5">All</text>
  <path d="M259 816.5 l2 2 2-2" fill="none" stroke="var(--white)" stroke-width=".8"/>
  <text class="m-small" x="667" y="808.5">Close</text>
  <path d="M690.5 804.5 l3.6 3.6 M694.1 804.5 l-3.6 3.6" stroke="var(--white)" stroke-width=".8"/>

  <text class="m-head" x="215" y="856">Short Term Memory</text>
  <rect class="chip-active" x="215" y="864" width="41" height="13" rx="6.5"/>
  <text class="chip-active-text" x="235.5" y="873.5">Grab</text>

  <text class="m-head" x="216.5" y="898">Working Memory</text>
  <g>
    <rect class="chip" x="216" y="908" width="43" height="13" rx="6.5"/><text class="chip-text" x="237.5" y="917">Cool Down</text>
    <rect class="chip" x="262" y="908" width="32" height="13" rx="6.5"/><text class="chip-text" x="278" y="917">Crave</text>
    <rect class="chip" x="298" y="908" width="33" height="13" rx="6.5"/><text class="chip-text" x="314.5" y="917">Go For</text>
    <rect class="chip" x="334" y="908" width="33" height="13" rx="6.5"/><text class="chip-text" x="350.5" y="917">Go-To</text>
    <rect class="chip" x="371" y="908" width="68" height="13" rx="6.5"/><text class="chip-text" x="405" y="917">In The Mood For</text>
    <rect class="chip" x="442" y="908" width="24" height="13" rx="6.5"/><text class="chip-text" x="454" y="917">Sip</text>
    <rect class="chip" x="470" y="908" width="45" height="13" rx="6.5"/><text class="chip-text" x="492.5" y="917">Soothing</text>
    <rect class="chip" x="519" y="908" width="51" height="13" rx="6.5"/><text class="chip-text" x="544.5" y="917">Strick With</text>
    <rect class="chip" x="575" y="908" width="84" height="13" rx="6.5"/><text class="chip-text" x="617" y="917">Throw in / Throw On</text>
  </g>

  <text class="m-head" x="216.5" y="943">Long Term Memory</text>
  <rect class="chip" x="215" y="951" width="49" height="13" rx="6.5"/>
  <text class="chip-text" x="239.5" y="960">Give it a Try</text>

  <text class="tag" x="845" y="1159" font-size="6.5">M1</text>
</svg>
</body>
</html>
```